Corvane Paintless Dent Removal

Our company works on vehicles removing dents using a highly skilled trade which the metal is massaged out with special tools without disturbing the original paint, hence paintless dent removal. Besides keeping the paint and metal original its also very environmentally friendly since no paint or toxic fillers are used. Also we we are one of the most experienced companies in the business with 25 years

Target Market(s)

Retail Automobile consumers, Auto Dealerships and Auto Body Shops

Industry/Entity Type

Auto Repair

Contact Information for Business Card

Dale Hollister
PO Box 518 Brookmere, NY 11962
631-555-0148
corvanepdr@mailbox-example.com
website corvanepdr.example
youtube corvane paintless dent removal
25 years of experience removing Dents, Dings and Hail Damage

Font styles to use
Serif
Sans Serif

Colors

Designer to choose colors to be used in the design.

Requirements
Must have
• I do like things that are simple but classy and somewhat bold, also I like my logo so that should be somewhat important

```html
<!DOCTYPE html>
<html lang="en">
<head>
<meta charset="utf-8">
<title>Corvane Paintless Dent Removal – Business Card</title>
<link rel="stylesheet" href="https://fonts.googleapis.com/css2?family=Roboto:wght@400;700;900&display=swap">
<style>
  :root {
    --navy: #13254a;
    --green: #7cc11f;
    --paper: #f4f4f4;
    --stage: #c9c9c9;
    --ink: #13254a;
    --white: #ffffff;
  }
  * { margin: 0; padding: 0; box-sizing: border-box; }
  html, body { width: 1200px; height: 576px; overflow: hidden; }
  body {
    background: var(--stage);
    font-family: "Roboto", Arial, sans-serif;
    position: relative;
  }
  .card {
    position: absolute;
    top: 138px;
    width: 484px;
    height: 294px;
    border-radius: 14px;
    overflow: hidden;
  }
  .card-front { left: 82px; background: var(--navy); }
  .card-back { left: 602px; background: var(--paper); }

  /* Front */
  .front-name {
    position: absolute;
    left: 0; right: 0; top: 108px;
    text-align: center;
    color: var(--white);
    font-weight: 900;
    line-height: 1;
  }
  .front-name .word { display: block; font-size: 46px; letter-spacing: -0.5px; }
  .front-name .tag { display: block; font-size: 16px; margin-top: 4px; }
  .front-url {
    position: absolute;
    left: 0; right: 0; top: 263px;
    display: flex; align-items: center; justify-content: center;
    gap: 18px;
    color: #dfe4ee;
    font-size: 13px;
    letter-spacing: 0.4px;
  }
  .front-url .rule { width: 90px; height: 2px; background: var(--green); }
  .front-url .hl { color: var(--green); }

  /* Back */
  .person { position: absolute; left: 25px; top: 36px; color: var(--ink); }
  .person-name { font-size: 22px; font-weight: 700; }
  .person-title { font-size: 12px; margin-top: 4px; }
  .back-name {
    position: absolute;
    left: 214px; top: 40px; width: 250px;
    text-align: center;
    color: var(--ink);
    font-weight: 900;
    line-height: 1;
  }
  .back-name .word { display: block; font-size: 32px; }
  .back-name .tag { display: block; font-size: 12px; margin-top: 3px; }
  .contact { position: absolute; left: 25px; top: 128px; color: var(--ink); font-size: 13px; }
  .contact-address { margin-bottom: 6px; }
  .contact-list { list-style: none; }
  .contact-list li { display: flex; align-items: center; height: 17px; }
  .contact-list svg { width: 12px; height: 12px; margin-right: 10px; flex: none; }
  .waves { position: absolute; left: 0; top: 0; width: 484px; height: 294px; }
  .experience {
    position: absolute;
    right: 20px; top: 220px;
    text-align: right;
    color: var(--white);
    font-size: 12px;
    line-height: 14.5px;
  }
</style>
</head>
<body>
  <section class="card card-front">
    <div class="front-name">
      <span class="word">CORVANE</span>
      <span class="tag">Paintless Dent Removal</span>
    </div>
    <div class="front-url">
      <span class="rule"></span>
      <span>www.<span class="hl">corvanepdr</span>.example</span>
      <span class="rule"></span>
    </div>
  </section>

  <section class="card card-back">
    <svg class="waves" viewBox="0 0 484 294" aria-hidden="true">
      <path fill="var(--navy)" d="M0,270 C90,262 170,248 250,208 C330,170 410,164 484,168 L484,294 L0,294 Z"/>
      <path fill="var(--green)" d="M0,236 C90,262 190,246 270,200 C350,160 420,148 484,148 L484,158 C410,158 340,172 262,210 C180,250 80,264 0,256 Z"/>
      <path fill="var(--green)" d="M40,262 C120,270 200,258 260,228 C200,266 120,276 40,262 Z"/>
    </svg>

    <div class="person">
      <div class="person-name">Dale Hollister</div>
      <div class="person-title">Managing Director</div>
    </div>

    <div class="back-name">
      <span class="word">CORVANE</span>
      <span class="tag">Paintless Dent Removal</span>
    </div>

    <div class="contact">
      <p class="contact-address">PO Box 518 Brookmere, NY 11962</p>
      <ul class="contact-list">
        <li>
          <svg viewBox="0 0 12 12" aria-hidden="true"><path fill="var(--green)" d="M1,4 C1,2 3,1 6,1 C9,1 11,2 11,4 L9,4.5 L8,3.5 L4,3.5 L3,4.5 Z M3,6 L9,6 L10,11 L2,11 Z"/></svg>
          631-555-0148
        </li>
        <li>
          <svg viewBox="0 0 12 12" aria-hidden="true"><rect x="1" y="2.5" width="10" height="7" fill="var(--green)"/><path d="M1,2.5 L6,7 L11,2.5" fill="none" stroke="var(--paper)" stroke-width="1"/></svg>
          corvanepdr@mailbox-example.com
        </li>
        <li>
          <svg viewBox="0 0 12 12" aria-hidden="true"><circle cx="6" cy="6" r="5" fill="none" stroke="var(--green)" stroke-width="1.4"/><path d="M1,6 H11 M6,1 C3.5,3.5 3.5,8.5 6,11 M6,1 C8.5,3.5 8.5,8.5 6,11" fill="none" stroke="var(--green)" stroke-width="1"/></svg>
          www.corvanepdr.example
        </li>
        <li>
          <svg viewBox="0 0 12 12" aria-hidden="true"><circle cx="6" cy="6" r="5" fill="var(--green)"/></svg>
          /Dale Hollister
        </li>
      </ul>
    </div>

    <p class="experience">25 years of<br>experience removing<br>Dents, Dings and Hail Damage</p>
  </section>
</body>
</html>
```